Business Card: RW Office Partners - Your organised problem solver

Business Name: RW Office Partners
Website: www.rwofficepartners.com.au
Email: marisol@rwofficepartners.com.au
Mobile: 61 482 907 236
Facebook: @rwofficepartners
Instrgram: @rwofficepartners

Brading Colours:
HEX
#986474
#ddccd3
#7a8498
#c9d8e4
#000000
#ffffff

Tag Line: Your organised problem solver

Link to DRAFT website:
https://deskhelpcollective.wixsite.com/rw-office-partners

About Page from the website:
My name is Marisol Wrenfield, and I would love to assist you to become more productive in your day to day and achieve your business and personal goals.
My mission is to give you time, time to work on the important tasks of your business or to be able to spend more time with your family. I will take on the tasks you don’t have time for, don’t know well or simply don’t like to do.
I have an extensive background in Administration, Tender Coordination, Document Control, WHS and Quality Management working primarily in the Construction, Mining and Corporate World.
I am passionate about being organised, having order and making things in your life (and mine) easier! I love to watch something unfold and grow into something amazing! I am known for being the go-to problem solver, the organiser of all things, producing high standards of work even under pressure. I’m also a confident communicator, and I understand that you’re busy running your business.

Target Market(s)

Small to Medium Business who require assistance in their business by a virtual assistant.

Industry/Entity Type

Virtual Assistant

Contact Information for Business Card

Mobile: 61 482 907 236

Font styles to use
Sans Serif

Colors
ffffff

Requirements
Must have
• Branding Colours as outlined.
Contact Details as outlined.
Logo as provided.
Proper contact details - mobile, facebook, instragm, website.
Simple, Elegant, very clean looking.
Should not have
• Note cute with pictures.
Not too girly as still want to market to construction companies.

```html
<!DOCTYPE html>
<html lang="en">
<head>
<meta charset="utf-8">
<title>RW Office Partners – Business Card</title>
<link rel="stylesheet" href="https://fonts.googleapis.com/css2?family=Roboto:wght@400;500;600&family=Kalam:wght@400&display=swap">
<style>
  :root {
    --brand-plum: #986474;
    --brand-plum-deep: #86545f;
    --brand-blush: #ddccd3;
    --brand-slate: #7a8498;
    --brand-mist: #c9d8e4;
    --ink: #222222;
    --paper: #f7f6f6;
    --backdrop: #e9e6e3;
    --white: #ffffff;
  }
  * { margin: 0; padding: 0; box-sizing: border-box; }
  html, body {
    width: 1200px;
    height: 1054px;
    overflow: hidden;
    background: var(--backdrop);
  }
  .canvas {
    position: relative;
    width: 1200px;
    height: 1054px;
  }
  .card {
    position: absolute;
    left: 100px;
    top: 227px;
    width: 1000px;
    height: 600px;
    border-radius: 24px;
    overflow: hidden;
    background: var(--paper);
    box-shadow: 0 10px 30px rgba(0, 0, 0, 0.12);
  }
  .card-backdrop {
    position: absolute;
    inset: 0;
    background: linear-gradient(120deg,
      var(--paper) 0%,
      var(--paper) 48%,
      var(--brand-slate) 53%,
      var(--brand-plum-deep) 59%,
      var(--brand-plum-deep) 100%);
  }

  .brand-name {
    position: absolute;
    left: 60px;
    top: 112px;
    font-family: "Roboto", sans-serif;
    font-weight: 600;
    font-size: 50px;
    letter-spacing: 0.5px;
    color: var(--brand-plum-deep);
    white-space: nowrap;
  }
  .tagline {
    position: absolute;
    left: 57px;
    top: 196px;
    font-family: "Kalam", cursive;
    font-size: 30px;
    color: var(--ink);
    white-space: nowrap;
  }

  .person {
    position: absolute;
    right: 45px;
    top: 256px;
    text-align: right;
    font-family: "Roboto", sans-serif;
  }
  .person-name {
    font-weight: 500;
    font-size: 36px;
    color: var(--brand-blush);
    line-height: 1.1;
  }
  .person-role {
    font-weight: 400;
    font-size: 23px;
    color: var(--white);
    margin-top: 6px;
  }

  .contact-list {
    position: absolute;
    right: 40px;
    top: 376px;
    list-style: none;
    font-family: "Roboto", sans-serif;
    font-size: 24px;
    color: var(--brand-blush);
  }
  .contact-item {
    display: flex;
    justify-content: flex-end;
    align-items: center;
    height: 38px;
    gap: 16px;
    white-space: nowrap;
  }
  .contact-icon {
    width: 22px;
    height: 22px;
    flex: none;
  }
  .contact-icon * { fill: none; stroke: var(--brand-blush); stroke-width: 2; }
  .contact-icon .solid { fill: var(--brand-blush); stroke: none; }
</style>
</head>
<body>
<main class="canvas">
  <article class="card">
    <div class="card-backdrop" role="img" aria-label="Decorative flowing plum and slate wave across the card"></div>

    <div class="brand-name">RW Office Partners</div>
    <p class="tagline">Your organised problem solver</p>

    <div class="person">
      <h1 class="person-name">Marisol Wrenfield</h1>
      <p class="person-role">Virtual Assistant</p>
    </div>

    <ul class="contact-list">
      <li class="contact-item">
        <span>61 482 907 236</span>
        <svg class="contact-icon" viewBox="0 0 22 22" aria-label="Phone">
          <path class="solid" d="M3,9 C3,5 19,5 19,9 L19,11 L15,11 L15,8.5 L7,8.5 L7,11 L3,11 Z"/>
          <path class="solid" d="M5,19 L6.5,11 L15.5,11 L17,19 Z"/>
        </svg>
      </li>
      <li class="contact-item">
        <span>@rwofficepartners</span>
        <svg class="contact-icon" viewBox="0 0 22 22" aria-label="Email">
          <rect x="2" y="5" width="18" height="12"/>
          <path d="M2,5 L11,12 L20,5"/>
        </svg>
      </li>
      <li class="contact-item">
        <span>@rwofficepartners</span>
        <svg class="contact-icon" viewBox="0 0 22 22" aria-label="Website">
          <circle cx="11" cy="11" r="8.5"/>
          <ellipse cx="11" cy="11" rx="3.8" ry="8.5"/>
          <path d="M2.5,11 H19.5 M4,6.5 H18 M4,15.5 H18"/>
        </svg>
      </li>
      <li class="contact-item">
        <span>www.rwofficepartners.com.au</span>
        <svg class="contact-icon" viewBox="0 0 22 22" aria-label="Social page">
          <rect class="solid" x="2" y="2" width="18" height="18" rx="3"/>
        </svg>
      </li>
      <li class="contact-item">
        <span>marisol@rwofficepartners.com.au</span>
        <svg class="contact-icon" viewBox="0 0 22 22" aria-label="Social profile">
          <rect x="3" y="3" width="16" height="16" rx="3"/>
        </svg>
      </li>
    </ul>
  </article>
</main>
</body>
</html>
```